Business Card Design Project

Business Card design based on logo.
Updates

I need business card, letterhead, envelope, and if possible, Powerpoint slide template.

On front of business card: Just logo- and  my name and title:  Harriet Lindqvist, Principal

On reverse-logo and the rest of the contact info:

4871 Quarry Lane
Davis, CA 95618
650-318-2764
hl@brackenstudyworks.example

On letterhead-Just logo at top, at bottom  the rest-very small along the bottom

On PPT slide-just the logo.

I also want to try a few other colors-I like lime/dark grey (not black) but would like to try Sienna, maybe also indigo or bright blue-green.

I forgot to add-

On the business card-switch to vertical on reverse side and put:

Reverse side-switch to vertical and list:

Harriet Lindqvist
Principal
Bracken Study Works, LLC

650-318-2764

4871 Quarry Lane
Davis, CA 95618

Harriet Lindqvist
Principal

650-318-2764

4871 Quarry Lane
Davis, CA 95618

I have another project at the same time-for Stationery. Feel free to submit to that one also.

That one includes letterhead, envelope, PPT slide, folder cover sheet-HL

Industry/Entity Type

Business

Requirements
Must have
• Must use logo-preferably lime green version-with gray, not black or just 2-tone -logo on colored background.

```html
<!DOCTYPE html>
<html lang="en">
<head>
<meta charset="utf-8">
<title>Bracken Study Works – Business Cards</title>
<link rel="stylesheet" href="https://fonts.googleapis.com/css2?family=Libre+Baskerville&family=Source+Sans+3:wght@400;600;700&display=swap">
<style>
  :root {
    --backdrop: #2b2b2c;
    --lime: #9cbb2f;
    --charcoal: #454547;
    --ink: #4a4a4c;
    --paper: #ffffff;
    --black: #111111;
  }
  * { box-sizing: border-box; margin: 0; padding: 0; }
  html, body { width: 1200px; height: 722px; overflow: hidden; }
  body {
    position: relative;
    background: var(--backdrop);
    font-family: "Source Sans 3", "Helvetica Neue", Arial, sans-serif;
  }
  .card {
    position: absolute;
    width: 525px;
    height: 300px;
    border-radius: 14px;
    overflow: hidden;
  }
  .card--front   { left: 62px;  top: 47px;  background: var(--paper); }
  .card--back    { left: 612px; top: 47px;  background: var(--paper); }
  .card--lime    { left: 62px;  top: 376px; height: 298px; background: var(--lime); }
  .card--dark    { left: 612px; top: 376px; height: 298px; background: var(--charcoal); }

  /* Brand name lockup: one colour, one weight, with a plain square */
  .brand {
    position: absolute;
    display: flex;
    flex-direction: column;
    align-items: center;
    font-family: "Source Sans 3", "Helvetica Neue", Arial, sans-serif;
    font-weight: 600;
    text-transform: uppercase;
    line-height: 1.05;
    text-align: center;
  }
  .brand__mark { display: block; width: 22px; height: 22px; margin-bottom: 12px; background: currentColor; }
  .brand__line { display: block; }

  .card--front .brand { left: 44px; top: 52px; width: 180px; color: var(--ink); font-size: 27px; letter-spacing: 3px; }
  .card--back  .brand { left: 0; right: 0; top: 58px; color: var(--ink); font-size: 40px; letter-spacing: 5px; }
  .card--lime  .brand { left: 0; right: 0; top: 80px; color: var(--black); font-size: 40px; letter-spacing: 5px; }
  .card--dark  .brand { left: 0; right: 0; top: 70px; color: var(--lime); font-size: 44px; letter-spacing: 6px; }
  .card--dark .brand__mark { width: 30px; height: 30px; margin-bottom: 18px; }

  .holder { position: absolute; right: 42px; top: 43px; text-align: center; }
  .holder__name { color: var(--lime); font-weight: 700; font-size: 17px; }
  .holder__title { color: var(--ink); font-size: 13px; margin-top: 2px; }

  .contacts { position: absolute; left: 43px; top: 180px; list-style: none; }
  .contacts li {
    display: flex; align-items: center; gap: 6px;
    height: 19px; color: var(--ink); font-size: 13.5px;
  }
  .contacts svg { width: 12px; height: 12px; fill: var(--lime); flex: none; }

  .front-rule { position: absolute; left: 0; right: 0; top: 261px; height: 3px; background: var(--lime); }
  .address-band {
    position: absolute; left: 0; right: 0; top: 266px; bottom: 0;
    background: var(--charcoal); color: var(--paper);
    font-size: 13.5px; padding: 8px 0 0 45px;
  }

  .web {
    position: absolute; left: 0; right: 0;
    text-align: center; font-size: 13px; letter-spacing: 2.2px;
  }
  .card--back .web { top: 221px; color: var(--ink); }
  .card--lime .web { top: 244px; color: var(--paper); }
  .card--dark .web { top: 244px; color: var(--paper); }
  .web__domain { color: var(--lime); }
  .card--lime .web__domain { color: var(--paper); }
</style>
</head>
<body>

  <section class="card card--front" aria-label="Business card front">
    <div class="brand">
      <span class="brand__mark"></span>
      <span class="brand__line">Bracken</span>
      <span class="brand__line">Study Works</span>
    </div>
    <div class="holder">
      <p class="holder__name">YOUR NAME</p>
      <p class="holder__title">Title</p>
    </div>
    <ul class="contacts">
      <li><svg viewBox="0 0 12 12"><path d="M2.5 1 4.5 3 3.6 4.6C4.3 6 6 7.7 7.4 8.4L9 7.5l2 2-1.5 1.5C5.5 10.5 1.5 6.5 1 2.5z"/></svg>0987 654321</li>
      <li><svg viewBox="0 0 12 12"><path d="M3.5 0.5h5a1 1 0 0 1 1 1v9a1 1 0 0 1-1 1h-5a1 1 0 0 1-1-1v-9a1 1 0 0 1 1-1zM3.5 2v7h5V2z"/></svg>0987 654321</li>
      <li><svg viewBox="0 0 12 12"><path d="M1 2.5h10v7H1zM1.6 3 6 6.3 10.4 3z"/></svg>info@brackenstudyworks.example</li>
      <li><svg viewBox="0 0 12 12"><path d="M6 1a5 5 0 1 0 0 10A5 5 0 0 0 6 1zm0 1.2c.8.8 1.3 2 1.4 3.2H4.6C4.7 4.2 5.2 3 6 2.2zM4.6 6.6h2.8C7.3 7.8 6.8 9 6 9.8 5.2 9 4.7 7.8 4.6 6.6z"/></svg>www.brackenstudyworks.example</li>
    </ul>
    <div class="front-rule"></div>
    <p class="address-band">00 Floor Complex Street City Name 000 111</p>
  </section>

  <section class="card card--back" aria-label="Business card back, white">
    <div class="brand">
      <span class="brand__mark"></span>
      <span class="brand__line">Bracken</span>
      <span class="brand__line">Study Works</span>
    </div>
    <p class="web">www.<span class="web__domain">brackenstudyworks</span>.example</p>
  </section>

  <section class="card card--lime" aria-label="Business card back, lime">
    <div class="brand">
      <span class="brand__mark"></span>
      <span class="brand__line">Bracken</span>
      <span class="brand__line">Study Works</span>
    </div>
    <p class="web">www.<span class="web__domain">brackenstudyworks</span>.example</p>
  </section>

  <section class="card card--dark" aria-label="Business card back, dark grey">
    <div class="brand">
      <span class="brand__mark"></span>
      <span class="brand__line">Bracken</span>
      <span class="brand__line">Study Works</span>
    </div>
    <p class="web">www.<span class="web__domain">brackenstudyworks</span>.example</p>
  </section>

</body>
</html>
```